One Page Website for Personal Trainer in London

I have a logo and need a one page website designed around my branding. I am a freelance Personal Trainer based in London specialising in bodyweight training for men and women. I would like the site to be modern and clean but not overtly urban in design.
I need the following headings:
About Me
My Services
Events
Blog
I don't need them to be seperate pages but if they can link to further down the page that would be great.
Industry/Entity Type
Personal Trainer
Coding
Coded - Design and coding required
Number of Pages Required
1 page
Requirements
Must have
- I need the following headings:
- About Me
- My Services
- Events
- Blog
- mobile friendly formatting
- health and fitness related photography
- Colour scheme in keeping with my existing logo

```html
<!DOCTYPE html>
<html lang="en">
<head>
<meta charset="utf-8">
<title>Marlow Reed – Personal Training</title>
<link href="https://fonts.googleapis.com/css2?family=Open+Sans:ital,wght@0,400;0,600;0,700;1,400;1,600&display=swap" rel="stylesheet">
<style>
:root{
  --orange:#f7941d;
  --orange-dark:#e07f0c;
  --ink:#2b2b2b;
  --text:#444;
  --muted:#8a8a8a;
  --light:#f2f2f2;
  --footer:#262626;
  --white:#fff;
}
*{margin:0;padding:0;box-sizing:border-box}
html,body{width:1200px;height:3965px;overflow:hidden}
body{position:relative;font-family:"Open Sans",Arial,sans-serif;color:var(--text);background:var(--white)}
.abs{position:absolute}
.topbar{left:0;top:0;width:1200px;height:12px;background:var(--ink)}
.header{left:0;top:12px;width:1200px;height:133px;background:var(--white)}
.brand{left:80px;top:60px;display:flex;align-items:center;gap:10px}
.brand-dot{width:22px;height:22px;border-radius:50%;background:var(--orange)}
.brand-name{font-size:24px;font-weight:600;color:var(--orange)}
.nav{right:80px;top:88px;display:flex;align-items:center;gap:22px;font-size:14px;color:var(--ink)}
.nav a{color:var(--ink);text-decoration:none}
.nav .active{background:var(--ink);color:var(--orange);padding:4px 22px;border-radius:14px}
.nav .sep{color:var(--muted);margin-left:-12px}
.hero{left:0;top:145px;width:1200px;height:727px;background:linear-gradient(100deg,#3b2e26 0%,#6b5646 35%,#7a6757 55%,#4a3b31 100%)}
.hero-shade{left:0;top:145px;width:1200px;height:727px;background:rgba(20,15,10,.35)}
.hero-text{left:0;top:485px;width:1200px;text-align:center;color:var(--white)}
.hero-text .pre{font-size:46px;font-weight:400;line-height:60px}
.hero-text .main{font-size:66px;font-weight:700;color:var(--orange);line-height:76px}
.hero-text .post{font-size:32px;line-height:44px}
.btn-hero{left:528px;top:692px;width:230px;height:50px;background:var(--orange);color:var(--white);font-size:18px;display:flex;align-items:center;justify-content:center}
.btn{display:flex;align-items:center;height:37px;font-size:11px;font-weight:700;text-transform:uppercase;letter-spacing:.5px}
.btn span{background:var(--orange);color:var(--white);height:100%;display:flex;align-items:center;padding:0 20px;flex:1;justify-content:center}
.btn i{width:30px;height:100%;background:var(--ink);display:block}
.about-photo{left:140px;top:991px;width:420px;height:317px;background:linear-gradient(135deg,#8f8f92,#4f4c4a 60%,#2f2c2a)}
.about-title{left:634px;top:980px;font-size:42px;font-weight:700;color:var(--ink)}
.about-sub{left:627px;top:1147px;width:420px;font-size:14px;font-weight:700;text-transform:uppercase;color:var(--ink);line-height:19px}
.about-copy{left:627px;top:1210px;width:420px;font-size:12px;line-height:19px;color:var(--muted)}
.about-btn{left:627px;top:1274px;width:153px}
.banner{left:0;top:1435px;width:1200px;height:476px;background:linear-gradient(90deg,#3a3a3c,#6d6e71 45%,#8d8e90 70%,#4d4d50)}
.banner-shade{left:0;top:1435px;width:1200px;height:476px;background:rgba(0,0,0,.3)}
.banner-text{left:0;top:1585px;width:1200px;text-align:center;color:var(--white)}
.banner-text .lead{font-size:20px;font-style:italic;font-weight:600}
.banner-text h2{font-size:56px;font-weight:600;line-height:62px;margin-top:8px}
.section-title{left:0;width:1200px;text-align:center;font-size:42px;font-weight:700}
.rule{left:580px;width:40px;height:3px;background:var(--orange)}
.svc-img{top:2088px;width:267px;height:177px}
.svc-name{top:2282px;width:267px;text-align:center;font-size:15px;font-weight:700;color:var(--orange)}
.svc-copy{top:2308px;width:267px;text-align:center;font-size:11px;line-height:15px;color:var(--text)}
.svc-btn{left:526px;top:2397px;width:151px}
.blog{left:0;top:2503px;width:1200px;height:714px;background:var(--orange)}
.card{top:2688px;width:267px;height:325px;background:var(--white);border-radius:6px;overflow:hidden}
.card-img{width:267px;height:188px}
.card-date{position:absolute;left:0;top:0;width:58px;height:58px;background:var(--orange);color:var(--white);text-align:center}
.card-date b{display:block;font-size:26px;line-height:34px}
.card-date small{font-size:9px}
.card h3{font-size:15px;font-weight:700;color:var(--ink);line-height:20px;padding:14px 18px 8px}
.card p{font-size:11px;line-height:15px;color:var(--muted);padding:0 18px}
.blog-btn{left:526px;top:3098px;width:240px}
.blog-btn span{background:var(--white);color:var(--orange)}
.lower{left:0;top:3217px;width:1200px;height:425px;background:var(--light)}
.col-title{top:3276px;font-size:26px;font-weight:600;color:var(--orange)}
.col-rule{top:3336px;height:1px;background:#cfcfcf}
.pager{top:3284px;display:flex;gap:6px}
.pager i{width:18px;height:18px;border-radius:50%;background:var(--orange);display:flex;align-items:center;justify-content:center}
.event{left:98px;width:470px;display:flex;gap:22px}
.event-date{width:58px;flex:none;text-align:center;color:var(--white)}
.event-date b{display:block;background:var(--ink);font-size:24px;line-height:42px}
.event-date span{display:block;background:var(--orange);font-size:14px;line-height:28px}
.event h4{font-size:15px;font-weight:600;color:var(--ink);margin-bottom:8px}
.event p{font-size:12px;line-height:17px;color:var(--text)}
.event-rule{left:98px;top:3458px;width:470px;height:1px;background:#d8d8d8}
.avatar{left:663px;top:3357px;width:138px;height:138px;border-radius:50%;border:5px solid var(--white);background:radial-gradient(circle at 50% 40%,#d9b8a0,#8a5f48)}
.avatar-name{left:663px;top:3505px;width:138px;text-align:center;font-size:11px;font-weight:700;color:var(--orange)}
.quote{left:838px;top:3367px;width:286px;font-size:12px;line-height:17px;color:var(--text)}
.quote::before,.quote::after{color:var(--orange);font-size:28px;font-weight:700;line-height:0;vertical-align:-8px}
.quote::before{content:"\201C";margin-right:4px}
.quote::after{content:"\201D";margin-left:4px}
.footer{left:0;top:3642px;width:1200px;height:323px;background:var(--footer);text-align:center}
.address{left:0;top:3714px;width:1200px;text-align:center;font-size:16px;font-weight:700;color:var(--white)}
.phone{left:0;top:3741px;width:1200px;text-align:center;font-size:16px;font-weight:700;color:var(--orange)}
.social{left:0;top:3814px;width:1200px;display:flex;justify-content:center;gap:22px}
.social i{width:14px;height:14px;border-radius:50%;background:var(--white);display:block}
.copyright{left:0;top:3920px;width:1200px;text-align:center;font-size:10px;color:#7d7d7d}
</style>
</head>
<body>
<div class="abs topbar"></div>
<header class="abs header"></header>
<div class="abs brand"><div class="brand-dot"></div><div class="brand-name">Marlow Reed</div></div>
<nav class="abs nav">
  <a class="active" href="#home">Home</a>
  <a href="#about">About Me</a>
  <a href="#services">My Services</a><span class="sep">|</span>
  <a href="#events">Events</a><span class="sep">|</span>
  <a href="#blog">Blog</a>
</nav>

<section id="home">
  <div class="abs hero" role="img" aria-label="Two women doing a bodyweight partner exercise in a gym, smiling"></div>
  <div class="abs hero-shade"></div>
  <div class="abs hero-text">
    <div class="pre">Start adding</div>
    <div class="main">Body weight Movements</div>
    <div class="post">into your training &amp; enjoy the results!</div>
  </div>
  <a class="abs btn-hero">Start training Now</a>
</section>

<section id="about">
  <div class="abs about-photo" role="img" aria-label="Woman crouching in a gym during a workout"></div>
  <h2 class="abs about-title">About us</h2>
  <p class="abs about-sub">Negare non possum. Dolore malum est: in crucem qui agitur, beatus esse non potest. Quae cum dixisset paulumque institisset</p>
  <p class="abs about-copy" style="top:1146px;visibility:hidden">.</p>
  <p class="abs about-copy" style="top:1196px">Lorem ipsum dolor sit amet, consectetur adipiscing elit. Dicimus aliquam huius viri. Tum singula copiose responderi solet, sed quae perspicua sunt longa esse non debent. Duo reges constructio harum quidem rerum facilis est et expedita distinctio. Ergo adhuc, quantum equidem intellego.</p>
  <div class="abs btn about-btn"><span>Read more</span><i></i></div>
</section>

<section>
  <div class="abs banner" role="img" aria-label="Man and woman doing bodyweight squats together in a bright studio"></div>
  <div class="abs banner-shade"></div>
  <div class="abs banner-text">
    <p class="lead">I am a freelance Personal Trainer based in London specialising in</p>
    <h2>Bodyweight training for<br>men and women.</h2>
  </div>
</section>

<section id="services">
  <h2 class="abs section-title" style="top:1965px;color:var(--ink)">Our Service</h2>
  <div class="abs rule" style="top:2043px"></div>

  <div class="abs svc-img" style="left:172px;background:linear-gradient(180deg,#b9cde0,#8aa6be 55%,#6b7d8c)" role="img" aria-label="Woman stretching on a beach"></div>
  <div class="abs svc-name" style="left:172px">Stretching</div>
  <p class="abs svc-copy" style="left:172px">Negare non possum. Dolore malum est: in crucem qui agitur, beatus esse</p>

  <div class="abs svc-img" style="left:468px;background:linear-gradient(135deg,#5d7fa8,#c9b7a8 55%,#6a4f45)" role="img" aria-label="Man lifting dumbbells on a bench"></div>
  <div class="abs svc-name" style="left:468px">Bodyweight Exercise</div>
  <p class="abs svc-copy" style="left:468px">Curiosorum. Putabam equidem satis, inquit, me dixisse. Quae diligentissime contra</p>

  <div class="abs svc-img" style="left:764px;top:2135px;height:133px;background:linear-gradient(135deg,#8e9aa3,#c24a4a 45%,#e0b23a 75%,#6d7c86)" role="img" aria-label="Fitness gear laid out: trainers, weights and a water bottle"></div>
  <div class="abs svc-name" style="left:764px">Fitness Plans</div>
  <p class="abs svc-copy" style="left:764px">Quodsi ipsam honestatem undique pertectam atque absolutam. Ut alios omittam.</p>

  <div class="abs btn svc-btn"><span>More service</span><i></i></div>
</section>

<section id="blog">
  <div class="abs blog"></div>
  <h2 class="abs section-title" style="top:2560px;color:var(--white)">Latest Blog</h2>
  <div class="abs rule" style="top:2636px;background:var(--white)"></div>

  <article class="abs card" style="left:42px">
    <div class="card-img" style="background:linear-gradient(135deg,#5aa6c8,#d47a8a 60%,#7b5b5b)" role="img" aria-label="Woman resting after an intense workout"></div>
    <div class="card-date"><b>22</b><small>October</small></div>
    <h3>Negare non possum. Dolore malum est</h3>
    <p>Negare non possum. Dolore malum est: in crucem qui agitur, beatus esse non potest.</p>
  </article>
  <article class="abs card" style="left:325px">
    <div class="card-img" style="background:linear-gradient(135deg,#9fb6cf,#c6b48f 55%,#5b4a3a)" role="img" aria-label="Two runners jogging outdoors"></div>
    <div class="card-date"><b>23</b><small>October</small></div>
    <h3>Quod autem satis est, eo quic uid accessit</h3>
    <p>Occurrentia nescio quae comminiscebantur. Dolor ergo, id est summum malum, metuetur semper, etiamsi abest.</p>
  </article>
  <article class="abs card" style="left:611px">
    <div class="card-img" style="background:linear-gradient(135deg,#c9c4c0,#4bbfd0 55%,#8f7a70)" role="img" aria-label="Woman holding small dumbbells in a fitness class"></div>
    <div class="card-date"><b>24</b><small>October</small></div>
    <h3>Alios in primisque familiarem nostrum Posidonium</h3>
    <p>Cognitio tamen Diogenem, Antipatrum, Mnesarchum, Panaetium, multos alios in primisque familiarem nostrum Posidonium vidimus.</p>
  </article>
  <article class="abs card" style="left:893px">
    <div class="card-img" style="background:linear-gradient(160deg,#f6d77a,#e99a3a 45%,#7a5a3a)" role="img" aria-label="Runner's feet on a trail at sunset"></div>
    <div class="card-date"><b>25</b><small>October</small></div>
    <h3>Vicimus. Hanc ergo intuens debet institutum</h3>
    <p>Quamquam id quidem, infinitum est in hac urbe. Nunc vides, quid faciat. Tum inquit.</p>
  </article>

  <div class="abs btn blog-btn"><span>View all blog posts</span><i></i></div>
</section>

<section id="events">
  <div class="abs lower"></div>
  <h2 class="abs col-title" style="left:92px">Events</h2>
  <div class="abs pager" style="left:510px">
    <i><svg width="8" height="8" viewBox="0 0 8 8"><path d="M5 1 2 4l3 3" fill="none" stroke="#fff" stroke-width="1.6"/></svg></i>
    <i><svg width="8" height="8" viewBox="0 0 8 8"><path d="M3 1l3 3-3 3" fill="none" stroke="#fff" stroke-width="1.6"/></svg></i>
  </div>
  <div class="abs col-rule" style="left:92px;width:476px"></div>

  <div class="abs event" style="top:3362px">
    <div class="event-date"><b>30</b><span>Oct</span></div>
    <div><h4>Verum tamen cum de rebus</h4><p>Lorem ipsum dolor sit amet, consectetur adipiscing elit. Quid utem habent admirationis.</p></div>
  </div>
  <div class="abs event-rule"></div>
  <div class="abs event" style="top:3472px">
    <div class="event-date"><b>31</b><span>Oct</span></div>
    <div><h4>Verum tamen cum de rebus</h4><p>Lorem ipsum dolor sit amet, consectetur adipiscing elit. Quid utem habent admirationis.</p></div>
  </div>

  <h2 class="abs col-title" style="left:660px">Testimonials</h2>
  <div class="abs pager" style="left:1077px">
    <i><svg width="8" height="8" viewBox="0 0 8 8"><path d="M5 1 2 4l3 3" fill="none" stroke="#fff" stroke-width="1.6"/></svg></i>
    <i><svg width="8" height="8" viewBox="0 0 8 8"><path d="M3 1l3 3-3 3" fill="none" stroke="#fff" stroke-width="1.6"/></svg></i>
  </div>
  <div class="abs col-rule" style="left:660px;width:463px"></div>
  <div class="abs avatar" role="img" aria-label="Portrait photo of client Hannah"></div>
  <div class="abs avatar-name">HANNAH</div>
  <p class="abs quote">Lorem ipsum dolor sit amet, consectetur adipiscing elit. Quid autem habent admirationis, cum prope accesseris? An hoc usque quaque, aliter in vita? Non igitur de improbo, sed de callido improbo quaerimus, qualis Q. Quae quibus rebus efficiuntur voluptates, eae non sunt in potestate sapientis.</p>
</section>

<footer>
  <div class="abs footer"></div>
  <p class="abs address">42 Kestrel Row, Camden, London NW1 8QT</p>
  <p class="abs phone">Phone (020) 7946 0813</p>
  <div class="abs social" aria-label="Social links"><i></i><i></i><i></i><i></i></div>
  <p class="abs copyright">© 2017 All rights reserved by Marlow Reed</p>
</footer>
</body>
</html>
```